New Email Marketing Design Project

I’d like you to make an email template. I’ll be welcoming and on boarding customers via email. And I’d like the branding to stand out. Keep it professional and simple. But be creative.

Design should look amazing on desktop and mobile phones.

Negative white space is ok.

Use stock images

I’ll like to have a spot for a picture of myself so make sure to include a circle where I can show my face so that email viewers will know who is speaking to them.

Target Market(s)

Practice managers, doctors, medical providers

Font styles to use
Sans Serif

Requirements
Must have
• Our Logo, CTA buttons, Same colors as website.
https://www.tarvoclaimservices.com

```html
<!DOCTYPE html>
<html lang="en">
<head>
<meta charset="utf-8">
<title>Tarvo Claim Services – Welcome Email</title>
<link rel="stylesheet" href="https://fonts.googleapis.com/css2?family=Fira+Sans:wght@600;700&family=Lato:wght@400&family=Montserrat:wght@300;600;700&family=Roboto:wght@400;700&display=swap">
<style>
  :root {
    --brand: #2f77a0;
    --brand-dark: #1f4f6c;
    --band: #4a4a4a;
    --ink: #222222;
    --muted: #9a9a9a;
    --paper: #ffffff;
    --stage: #e4e4e4;
  }
  * { box-sizing: border-box; margin: 0; padding: 0; }
  html, body { width: 1200px; height: 1200px; overflow: hidden; background: var(--stage); }
  .email {
    position: absolute; left: 50%; top: 50%;
    width: 886px; height: 1335px;
    transform: translate(-50%, -50%) scale(0.87);
    background: var(--paper);
    font-family: "Lato", sans-serif;
    color: var(--muted);
  }
  .abs { position: absolute; }

  /* header */
  .brand-mark { left: 22px; top: 18px; width: 34px; height: 34px; border-radius: 50%; border: 3px solid var(--brand); }
  .brand-name { left: 86px; top: 24px; font: 700 20px "Fira Sans", sans-serif; color: var(--brand); }
  .help-icon { left: 506px; top: 18px; }
  .help-label { left: 534px; top: 17px; font: 400 11px "Roboto", sans-serif; color: var(--ink); }
  .help-number { left: 534px; top: 35px; font: 700 15px "Roboto", sans-serif; color: var(--ink); letter-spacing: .5px; }
  .cta { left: 734px; top: 16px; width: 138px; height: 37px; background: var(--brand); color: #fff;
    font: 700 14px "Roboto", sans-serif; display: flex; align-items: center; justify-content: center; gap: 7px; }

  /* hero */
  .hero-photo { left: 0; top: 67px; width: 886px; height: 533px;
    background: linear-gradient(120deg, #c9d9e6 0%, #e9eef2 45%, #f6f7f8 70%, #dfe6ee 100%); }
  .hero-tint { left: 0; top: 67px; }
  .hero-title { left: 44px; top: 352px; font: 700 72px/1 "Montserrat", sans-serif; color: #fff; letter-spacing: -1px; }
  .hero-sub { left: 44px; top: 440px; font: 300 72px/1 "Montserrat", sans-serif; color: var(--brand-dark); letter-spacing: -1px; }
  .hero-band { left: 2px; top: 600px; width: 882px; height: 51px; background: var(--band); }
  .portrait { left: 594px; top: 514px; width: 240px; height: 240px; border-radius: 50%;
    border: 6px solid var(--brand); background: radial-gradient(circle at 50% 40%, #e8edf1 0%, #b9c8d4 70%, #8ea4b5 100%); }

  /* content */
  .section-title { font: 700 30px "Fira Sans", sans-serif; color: var(--brand); }
  .body-copy { font: 400 14px/18px "Lato", sans-serif; color: var(--muted); }
  .about-title { left: 56px; top: 703px; }
  .about-copy { left: 56px; top: 741px; width: 452px; }
  .services-title { left: 56px; top: 858px; }
  .services-copy { left: 56px; top: 896px; width: 770px; }

  .service { width: 128px; text-align: left; }
  .service svg { display: block; margin: 0 auto 10px; }
  .service p { font: 400 7px/8.5px "Lato", sans-serif; color: var(--muted); }

  .rise-label { left: 56px; top: 1090px; font: 600 11px "Montserrat", sans-serif; color: var(--muted); text-transform: uppercase; }
  .rise-copy { left: 56px; top: 1108px; width: 770px; font: 600 11.5px/22px "Montserrat", sans-serif; color: #a6a6a6; }

  .contact { top: 1226px; display: flex; align-items: center; gap: 8px;
    font: 700 9px/11px "Montserrat", sans-serif; color: var(--ink); }

  .footer { left: 0; top: 1270px; width: 886px; height: 65px; background: var(--brand); }
  .social { top: 1281px; width: 34px; height: 34px; border-radius: 50%; border: 2px solid #1d2f3b; }
</style>
</head>
<body>
<main class="email">
  <header>
    <span class="abs brand-mark"></span>
    <span class="abs brand-name">Tarvo Claim Services</span>
    <svg class="abs help-icon" width="16" height="34" viewBox="0 0 16 34" aria-hidden="true">
      <rect x="1.5" y="1.5" width="13" height="31" rx="2.5" fill="none" stroke="#1d4fa0" stroke-width="3"/>
      <rect x="5" y="28" width="6" height="2" fill="#1d4fa0"/>
    </svg>
    <span class="abs help-label">Need Help? Call Us Now</span>
    <span class="abs help-number">16125550148</span>
    <a class="abs cta">GET IN TOUCH
      <svg width="13" height="13" viewBox="0 0 13 13" aria-hidden="true">
        <circle cx="6.5" cy="6.5" r="6.5" fill="#fff"/>
        <path d="M4 6.5h4.5M6.5 4l2.5 2.5-2.5 2.5" stroke="#2f77a0" stroke-width="1.8" fill="none"/>
      </svg>
    </a>
  </header>

  <section class="hero">
    <div class="abs hero-photo" role="img" aria-label="Stock photo of a person writing notes at a desk beside a laptop and a small plant"></div>
    <svg class="abs hero-tint" width="886" height="533" aria-hidden="true">
      <polygon points="0,0 312,0 535,533 0,533" fill="#6f9ec4" opacity="0.55"/>
    </svg>
    <h1 class="abs hero-title">Tarvo Claim</h1>
    <p class="abs hero-sub">Services</p>
    <div class="abs hero-band"></div>
    <div class="abs portrait" role="img" aria-label="Circular portrait of the sender"></div>
  </section>

  <section>
    <h2 class="abs section-title about-title">About Us</h2>
    <p class="abs body-copy about-copy">Ea consul insolens interesset usu, id ius nihil nostrum tacimates. Eu mu alii quando epicurei. Ut eum lorem rationibus. In ius nobis accommoda uat conceptam ei sea, at prompta qualisque corrumpit vel. Nec ea dign et noluisse splendide duo. No ius zril adversarium, cu</p>

    <h2 class="abs section-title services-title">Our Services</h2>
    <p class="abs body-copy services-copy">Ea consul insolens interesset usu, id ius nihil nostrum tacimates. Eu mu&nbsp; eresset usu, id ius nihil nostrum tacimates. Eu mu alii quando epicurei. Ut eum lorem rationibus. In ius nobis accommodaUt eum lorem rationibus. In ius nobis a</p>

    <div class="abs service" style="left:64px; top:975px;">
      <svg width="34" height="42" viewBox="0 0 34 42" aria-hidden="true">
        <path d="M2 2h22l8 8v30H2z" fill="none" stroke="#2f77a0" stroke-width="2.5"/>
        <path d="M8 12h16M8 18h18M8 24h18M8 30h18" stroke="#2f77a0" stroke-width="2.5"/>
      </svg>
      <p>Accurate claim coding and review so every visit is billed right the first time.</p>
    </div>
    <div class="abs service" style="left:273px; top:975px;">
      <svg width="40" height="42" viewBox="0 0 40 42" aria-hidden="true">
        <circle cx="24" cy="16" r="12" fill="none" stroke="#2f77a0" stroke-width="4"/>
        <path d="M15 25L4 38" stroke="#2f77a0" stroke-width="6" stroke-linecap="round"/>
      </svg>
      <p>Denial research that finds the root cause and gets your payments back on track.</p>
    </div>
    <div class="abs service" style="left:488px; top:975px;">
      <svg width="40" height="42" viewBox="0 0 40 42" aria-hidden="true">
        <circle cx="20" cy="24" r="15" fill="none" stroke="#2f77a0" stroke-width="3.5"/>
        <path d="M16 4h8M20 4v5M20 24l6-6" stroke="#2f77a0" stroke-width="3.5" stroke-linecap="round"/>
      </svg>
      <p>Fast turnaround on submissions, follow-ups and payer calls to shorten your cash cycle.</p>
    </div>
    <div class="abs service" style="left:691px; top:975px;">
      <svg width="46" height="42" viewBox="0 0 46 42" aria-hidden="true">
        <path d="M23 2L1 22h7v18h11V28h8v12h11V22h7z" fill="#2f77a0"/>
      </svg>
      <p>Remote billing support for practices of any size, working as part of your team.</p>
    </div>

    <p class="abs rise-label">Remote medical billing work on the rise</p>
    <p class="abs rise-copy">Remote medical billing work on the rise thanks to COVID-19. Most people are not ready to risk bringing contagion home to their families. Rightfully so, they are choosing to not work at places where there are large crowds or many customers. Preferring smaller less trafficked setting. The trend is only going to continue as new platforms are made available every single week. It has been determined that outsourcing is the way of the future for medical billing. Is your practice on</p>
  </section>

  <section>
    <div class="abs contact" style="left:54px;">
      <svg width="20" height="27" viewBox="0 0 20 27" aria-hidden="true">
        <path d="M10 1C5 1 1 5 1 10c0 7 9 16 9 16s9-9 9-16c0-5-4-9-9-9z" fill="#2f77a0"/>
        <circle cx="10" cy="10" r="3.5" fill="#fff"/>
      </svg>
      <span>210 Harbor Ridge Ave Ste 400,<br>Lakemont, Minnesota 55990</span>
    </div>
    <div class="abs contact" style="left:268px;">
      <svg width="16" height="28" viewBox="0 0 16 28" aria-hidden="true">
        <rect x="1.5" y="1.5" width="13" height="25" rx="2.5" fill="none" stroke="#2f77a0" stroke-width="2.5"/>
        <rect x="6" y="22" width="4" height="2" fill="#2f77a0"/>
      </svg>
      <span>612-555-0148</span>
    </div>
    <div class="abs contact" style="left:361px;">
      <svg width="26" height="24" viewBox="0 0 26 24" aria-hidden="true">
        <rect x="7" y="1" width="12" height="8" fill="#2f77a0"/>
        <rect x="1" y="8" width="24" height="15" rx="2" fill="#2f77a0"/>
        <path d="M6 13h3M11 13h3M16 13h3M6 17h3M11 17h3M16 17h3" stroke="#fff" stroke-width="1.6"/>
      </svg>
      <span>612-555-0148</span>
    </div>
    <div class="abs contact" style="left:468px;">
      <svg width="24" height="16" viewBox="0 0 24 16" aria-hidden="true">
        <rect x="1" y="1" width="22" height="14" fill="none" stroke="#2f77a0" stroke-width="2"/>
        <path d="M1 1l11 8 11-8" fill="none" stroke="#2f77a0" stroke-width="2"/>
      </svg>
      <span>hello@tarvoclaimservices.com</span>
    </div>
  </section>

  <footer>
    <div class="abs footer"></div>
    <span class="abs social" style="left:669px;"></span>
    <span class="abs social" style="left:714px;"></span>
    <span class="abs social" style="left:759px;"></span>
    <span class="abs social" style="left:804px;"></span>
  </footer>
</main>
</body>
</html>
```